Tandem Hearth Works Pty Ltd

We need business cards for a company based in Perth, we install, service and maintain fire equipment.
On the front we want a great design with our logo and a small spot for our full company name, general company email address and office number. On the back we need space for our name, title, mobile number and email address on the back.

Target Market(s)

Facility managers and commercial/industrial building owners/occupiers.

Contact Information for Business Card

Font styles to use
Sans Serif

Requirements
Must have
• Please only submit 5 of your best samples.
Darker tones are preferred.
Nice to have
• We want to use, black, red and grey. Keep it modern and clean.
I've attached the company logo and a sample of a boarder we use on our emergency plans.
Should not have
• No preference. Let the designer choose.

```html
<!DOCTYPE html>
<html lang="en">
<head>
<meta charset="utf-8">
<title>Tandem Hearth Works – Business Cards</title>
<link href="https://fonts.googleapis.com/css2?family=Roboto:wght@400;700&display=swap" rel="stylesheet">
<style>
  :root {
    --page-bg: #000000;
    --card-bg: #2f3033;
    --card-edge: #3a3b3e;
    --brand-red: #e8212a;
    --text-grey: #c9c9cb;
    --divider: #55565a;
  }
  * { box-sizing: border-box; margin: 0; padding: 0; }
  html, body {
    width: 1200px; height: 900px; overflow: hidden;
    background: var(--page-bg);
    font-family: "Roboto", Arial, sans-serif;
  }
  .stage { position: relative; width: 1200px; height: 900px; }
  .card {
    position: absolute;
    width: 458px; height: 282px;
    background: linear-gradient(180deg, var(--card-edge) 0%, var(--card-bg) 60%);
    border-radius: 14px;
  }
  .card--person { left: 138px; top: 265px; }
  .card--company { left: 625px; top: 268px; }
  .wordmark {
    position: absolute; left: 72px; top: 102px;
    width: 114px; text-align: center;
    font-weight: 700; font-size: 52px; line-height: 1;
    color: var(--brand-red); letter-spacing: 1px;
  }
  .card--company .wordmark { left: 73px; top: 104px; }
  .divider {
    position: absolute; left: 217px; width: 1px;
    background: var(--divider);
  }
  .card--person .divider { top: 97px; height: 89px; }
  .card--company .divider { top: 86px; height: 108px; }
  .details { position: absolute; left: 240px; }
  .card--person .details { top: 96px; }
  .card--company .details { top: 85px; left: 241px; }
  .person-name, .company-name {
    color: var(--brand-red); font-weight: 700;
    font-size: 18px; line-height: 20px; text-transform: uppercase;
  }
  .person-title { color: var(--text-grey); font-size: 13.5px; margin-top: 1px; }
  .office-phone {
    color: var(--text-grey); font-weight: 700;
    font-size: 19px; margin-top: 5px; margin-left: -2px;
  }
  .contact-list { list-style: none; }
  .card--person .contact-list { margin-top: 20px; }
  .card--company .contact-list { margin-top: 3px; }
  .contact-list li {
    display: flex; align-items: center; gap: 7px;
    color: var(--text-grey); font-size: 13.5px; line-height: 17px;
  }
  .contact-list svg { width: 12px; height: 12px; flex: none; fill: var(--brand-red); }
</style>
</head>
<body>
<div class="stage">

  <section class="card card--person">
    <div class="wordmark">THW</div>
    <div class="divider"></div>
    <div class="details">
      <h1 class="person-name">Marcus Ellery</h1>
      <p class="person-title">Managing Director</p>
      <ul class="contact-list">
        <li>
          <svg viewBox="0 0 12 12" aria-hidden="true"><path d="M3 0h6a1 1 0 0 1 1 1v10a1 1 0 0 1-1 1H3a1 1 0 0 1-1-1V1a1 1 0 0 1 1-1zm0 1.5v7.5h6V1.5zM6 10a.6.6 0 1 0 0 1.2A.6.6 0 0 0 6 10z"/></svg>
          555.0134.2281
        </li>
        <li>
          <svg viewBox="0 0 12 12" aria-hidden="true"><path d="M0 2.5h12v7H0zM1 3.2l5 3.6 5-3.6v-.1H1z" fill-rule="evenodd"/></svg>
          name@thw.com
        </li>
      </ul>
    </div>
  </section>

  <section class="card card--company">
    <div class="wordmark">THW</div>
    <div class="divider"></div>
    <div class="details">
      <h2 class="company-name">Tandem Hearth<br>Works Pty Ltd</h2>
      <p class="office-phone">555.0190.4470</p>
      <ul class="contact-list">
        <li>
          <svg viewBox="0 0 12 12" aria-hidden="true"><path d="M0 2.5h12v7H0zM1 3.2l5 3.6 5-3.6v-.1H1z" fill-rule="evenodd"/></svg>
          info@thw.com
        </li>
        <li>
          <svg viewBox="0 0 12 12" aria-hidden="true"><path d="M6 0a6 6 0 1 0 0 12A6 6 0 0 0 6 0zm0 1c.6.6 1.1 1.6 1.3 2.9H4.7C4.9 2.6 5.4 1.6 6 1zM1.1 5h2.5v2H1.1a5 5 0 0 1 0-2zm3.6 0h2.6v2H4.7zm3.7 0h2.5a5 5 0 0 1 0 2H8.4zM4.7 8h2.6c-.2 1.3-.7 2.3-1.3 2.9C5.4 10.4 4.9 9.3 4.7 8z"/></svg>
          www.thw.com
        </li>
      </ul>
    </div>
  </section>

</div>
</body>
</html>
```